Wordpress 6 pages GLAM design for hair salon

Hi guys.
I need a glam & easy to navigate web design for my (women only) new hair salon.
I have a logo. You can see in attached files.
I like 3d backgrounds.
My favourite colours choice: any variety of pink(hot & very soft), white, black, grey.
I would like to see website very feminine, glamorous & kind of old Hollywood and Dorinda Calloway inspired.
Of course it should have plug ins, like social media, map, security etc.
My website now: http://velmoracoiffure.example

Designs what I like:
http://torvinellastudio.example
http://pelurabeautyloft.example
http://www.quillfernvisualworks.example/boutique-graphic-web-folio.html
Updates

Target Market(s)

WOMEN

Industry/Entity Type

Boutique

Requirements
Should not have
• any cartoon or other characters!

```html
<!DOCTYPE html>
<html lang="en">
<head>
<meta charset="utf-8">
<title>Velmora Coiffure – About Us</title>
<link href="https://fonts.googleapis.com/css2?family=Oswald:wght@600&family=Open+Sans:wght@400;700&family=Great+Vibes&display=swap" rel="stylesheet">
<style>
  :root {
    --stripe-light: #f7c9d6;
    --stripe-dark: #efb3c5;
    --panel-pink: #f6b6c8;
    --hot-pink: #e8198b;
    --ink: #222222;
    --body-text: #3a3a3a;
    --white: #ffffff;
    --black: #141414;
    --soft-pink: #f3a9bf;
  }
  * { box-sizing: border-box; margin: 0; padding: 0; }
  html, body { width: 1200px; height: 675px; overflow: hidden; }
  body {
    position: relative;
    font-family: "Open Sans", sans-serif;
    color: var(--body-text);
    background: repeating-linear-gradient(90deg,
      var(--stripe-light) 0 30px, var(--stripe-dark) 30px 62px);
  }
  .main-nav {
    position: absolute; top: 0; left: 0; width: 1200px; height: 70px;
  }
  .main-nav a {
    position: absolute; top: 29px;
    font-family: "Oswald", sans-serif; font-weight: 600;
    font-variant: small-caps; font-size: 21px; letter-spacing: 0.5px;
    color: var(--black); text-decoration: none; line-height: 24px;
  }
  .main-nav a.is-active { padding: 0 10px; }
  .main-nav a.is-active::before,
  .main-nav a.is-active::after {
    content: ""; position: absolute; left: 0; right: 0; height: 1px; background: var(--black);
  }
  .main-nav a.is-active::before { top: -7px; }
  .main-nav a.is-active::after { bottom: -6px; }

  .content-panel {
    position: absolute; left: 101px; top: 70px; width: 984px; height: 620px;
    background: var(--panel-pink);
    box-shadow: 0 0 14px rgba(120, 40, 70, 0.35);
  }
  .content-body {
    position: absolute; left: 9px; top: 9px; width: 966px; height: 611px;
    background: var(--white); overflow: hidden;
  }
  .hero {
    width: 966px; height: 264px;
    background: linear-gradient(180deg, #d9d9d9 0%, #8c8c8c 45%, #2b2b2b 100%);
  }

  .brand {
    position: absolute; left: 493px; top: -22px; width: 194px; height: 194px;
    border-radius: 50%; background: var(--black);
    border: 6px solid var(--soft-pink);
    display: flex; align-items: center; justify-content: center;
  }
  .brand-name {
    font-family: "Open Sans", sans-serif; font-weight: 700;
    font-size: 25px; color: var(--white); letter-spacing: 0.5px;
    text-align: center; line-height: 1.15; margin-top: 30px;
  }

  .profile {
    position: absolute; left: 9px; top: 282px; width: 206px; text-align: center;
  }
  .profile-photo {
    display: block; width: 123px; height: 172px; margin: 0 auto;
    background: linear-gradient(180deg, #3a2a22 0%, #c99a80 50%, #1b1b1b 100%);
  }
  .profile-name {
    margin-top: 22px; font-weight: 700; font-size: 16.5px; color: var(--ink);
  }
  .profile-role { margin-top: 6px; font-size: 13px; color: var(--body-text); }

  .about {
    position: absolute; left: 250px; top: 282px; width: 670px;
  }
  .about h1 {
    font-weight: 700; font-size: 28px; color: var(--hot-pink); line-height: 1.2;
  }
  .highlights {
    margin-top: 45px; padding-left: 37px; font-size: 12.6px; line-height: 18.4px;
  }
  .about h2 {
    margin-top: 17px; font-size: 12.6px; font-weight: 700; color: var(--ink); line-height: 18.4px;
  }
  .about p { font-size: 12.6px; line-height: 18.4px; }
</style>
</head>
<body>
  <nav class="main-nav">
    <a href="#" style="left:136px">Home</a>
    <a href="#" class="is-active" style="left:218px">About Us</a>
    <a href="#" style="left:346px">Services</a>
    <a href="#" style="left:778px">Gallery</a>
    <a href="#" style="left:892px">Blog</a>
    <a href="#" style="left:979px">Contacts</a>
  </nav>

  <main class="content-panel">
    <div class="content-body">
      <div class="hero" role="img" aria-label="Photo of the salon interior with black styling chairs and mirrored stations"></div>

      <aside class="profile">
        <span class="profile-photo" role="img" aria-label="Portrait photo of the stylist"></span>
        <h3 class="profile-name">LIORA VANTESSE</h3>
        <div class="profile-role">Hair Stylist</div>
      </aside>

      <section class="about">
        <h1>A Few Words About Me</h1>
        <ul class="highlights">
          <li>Certified Hair Stylist with European and Canadian experience</li>
          <li>Finalist of the Lumina 2013 - The Canadian Hairstylist of the Year Awards.</li>
          <li>Leading Stylist at fashion shows and photo shoots</li>
          <li>Trained by World Class Halcrest Beauty School, Orwen Styling Academy (Canada), Strandelle Hair Extensions Certification (Canada), Colorea School (Italy), European Hairstyle School, Veskor School (Europe)</li>
        </ul>
        <h2>The Stylist/colorist</h2>
        <p>A professional stylist/colorist is fundamentally different from the classic hairdresser. The name of the profession comes from the word” color”, because the colorist specializes in hair coloring. Moreover, the procedure of dying with colorist has an independent title “coloring” to emphasize the difference from the classical multi-tone hair coloring. The stylist/colorist selects not one color, but the range of matching colors, taking into account not only the wishes of the client, but also the color of his eyes and skin.</p>
        <p>There are many important things in the stylist/colorist profession: knowledge of chemistry, physics, and</p>
      </section>
    </div>
  </main>

  <div class="brand">
    <div class="brand-name">VELMORA<br>COIFFURE</div>
  </div>
</body>
</html>
```